A multi-page brochure that explains our firm ,KVL Wealth Management

We have a current brochure attached but it is a compilation of several items combined into one. We would like this to have the same content but be one complete theme. We are a financial planning form so it needs to have a level of professionalism but also a comfortable approach for clients and showing that was have a lot of resources and experience. We cater mostly to the 55-60+ age community.

We need the front page picture changed. lake themed would be great, like our website www.TheMoskaHouse.com
Just to be clear we use KVL Wealth Management now as our company name. Parent company name is The Moska House LLC. I attached the current mock brochure and our new logos.
Our logo colors are:
KVL WM Logo Colors:

Blue:
HEX: #0f75bc
RGB: rgba(15,117,188,255)

Grey:
HEX: #6d6e71
RGB: rgba(109,110,113,255)

Target Market(s)

High-level individuals that are looking for financial guidance who are 40 years old and up

Industry/Entity Type

Wealth Management

Requirements
Must have
• Clean and crisp
Nice to have
• https://www.bramblestoneplanners.com/wealth-management-brochure , this is a sample we like

```html
<!DOCTYPE html>
<html lang="en">
<head>
<meta charset="utf-8">
<title>KVL Wealth Management Brochure</title>
<link rel="stylesheet" href="https://fonts.googleapis.com/css2?family=Poppins:ital,wght@0,400;0,600;0,700;1,400;1,600;1,700&display=swap">
<style>
  :root{
    --brand-blue:#0f75bc;
    --brand-grey:#6d6e71;
    --shape-grey:#555657;
    --ink:#111111;
    --body-ink:#333333;
    --panel:#efefef;
    --backdrop:#555555;
    --white:#ffffff;
  }
  *{margin:0;padding:0;box-sizing:border-box;}
  html,body{width:1200px;height:522px;overflow:hidden;background:var(--backdrop);}
  body{font-family:"Poppins",sans-serif;}
  .spread{position:absolute;left:0;top:0;width:2576px;height:1120px;transform:scale(0.46584);transform-origin:0 0;}
  .page{position:absolute;top:30px;width:825px;height:1067px;background:var(--white);overflow:hidden;}
  .page--cover{left:20px;}
  .page--specialist{left:872px;}
  .page--firm{left:1723px;}
  .page-art{position:absolute;left:0;top:0;width:825px;height:1067px;}
  .page-footer{position:absolute;left:0;bottom:0;width:825px;height:54px;background:var(--brand-blue);color:var(--white);
    font-size:21px;letter-spacing:3.5px;text-align:right;padding-right:28px;line-height:54px;}

  /* cover */
  .brand-name{position:absolute;left:35px;top:752px;display:flex;align-items:center;gap:14px;
    font-size:40px;font-weight:600;color:var(--brand-blue);letter-spacing:0.5px;}
  .brand-mark{width:22px;height:22px;background:var(--brand-blue);}
  .cover-title{position:absolute;left:35px;top:832px;font-size:50px;line-height:53px;font-weight:700;color:var(--ink);}
  .accent{color:var(--brand-blue);font-style:italic;}

  /* section heads */
  .section-title{position:absolute;font-weight:700;color:var(--ink);font-size:42px;line-height:48px;}
  .swoosh{position:absolute;width:128px;height:26px;}

  .specialist-title{left:35px;top:514px;}
  .specialist-swoosh{left:35px;top:622px;}
  .body-copy{position:absolute;color:var(--body-ink);font-size:15px;line-height:28.3px;letter-spacing:0;}
  .specialist-intro{left:35px;top:668px;width:640px;}
  .specialist-outro{left:35px;top:852px;width:770px;}

  .firm-title{left:30px;top:38px;font-size:42px;}
  .firm-swoosh{left:30px;top:98px;}
  .firm-intro{left:30px;top:138px;width:540px;font-size:15px;line-height:24.5px;}
  .firm-intro p+p{margin-top:7px;}

  .principles{position:absolute;left:30px;top:278px;display:flex;gap:20px;}
  .principle{width:242px;height:220px;background:var(--panel);padding:20px 13px 0 13px;}
  .principle-icon{width:42px;height:34px;display:block;}
  .principle-name{font-size:21px;font-weight:700;color:var(--brand-blue);margin-top:4px;line-height:30px;}
  .principle-text{font-size:12.3px;line-height:19px;color:var(--body-ink);margin-top:6px;}

  .firm-copy{position:absolute;left:30px;top:526px;width:760px;}
  .firm-body{font-size:15px;line-height:24.4px;text-align:justify;color:var(--body-ink);}
  .firm-note{margin-top:12px;font-size:12.6px;line-height:21px;font-style:italic;color:var(--brand-blue);}

  .firm-photo{position:absolute;top:717px;width:376px;height:270px;}
  .firm-photo--glass{left:30px;background:linear-gradient(160deg,#4f8fd3 0%,#8ec1ea 35%,#3f7db8 65%,#5b8a5a 100%);}
  .firm-photo--modern{left:420px;background:linear-gradient(170deg,#3a6fb0 0%,#8aa6c8 40%,#4b4f57 70%,#2f3236 100%);}
</style>
</head>
<body>
<div class="spread">

  <!-- Cover -->
  <section class="page page--cover">
    <svg class="page-art" viewBox="0 0 825 1067">
      <defs>
        <linearGradient id="lakeScene" x1="0" y1="0" x2="0" y2="1">
          <stop offset="0" stop-color="#2f8fe0"/>
          <stop offset="0.3" stop-color="#8fb8d8"/>
          <stop offset="0.5" stop-color="#7c7360"/>
          <stop offset="0.68" stop-color="#3fc1c0"/>
          <stop offset="1" stop-color="#8a7a66"/>
        </linearGradient>
      </defs>
      <polygon points="0,0 230,0 250,470 0,718" fill="var(--brand-blue)"/>
      <polygon points="825,410 825,650 715,538" fill="var(--brand-blue)"/>
      <polygon points="200,0 825,0 825,420 520,718 0,200" fill="url(#lakeScene)" stroke="var(--white)" stroke-width="12" role="img" aria-label="Mountain lake with turquoise water, pine trees and snowy peaks"/>
      <polygon points="270,470 390,594 270,716 150,594" fill="var(--shape-grey)" stroke="var(--white)" stroke-width="10"/>
    </svg>
    <div class="brand-name"><span class="brand-mark"></span>KVL Wealth Management</div>
    <h1 class="cover-title">Wealth Management<br><span class="accent">Focused</span> on Your <span class="accent">Needs</span><br><span class="accent">and Vision</span></h1>
    <footer class="page-footer">www.themoskahouse.com</footer>
  </section>

  <!-- Partner with a Specialist -->
  <section class="page page--specialist">
    <svg class="page-art" viewBox="0 0 825 1067">
      <defs>
        <linearGradient id="officeScene" x1="0" y1="0" x2="1" y2="1">
          <stop offset="0" stop-color="#5a4a40"/>
          <stop offset="0.4" stop-color="#9a8f86"/>
          <stop offset="0.7" stop-color="#c9b79f"/>
          <stop offset="1" stop-color="#6d6760"/>
        </linearGradient>
      </defs>
      <polygon points="698,0 825,0 825,365 580,122" fill="var(--brand-blue)"/>
      <polygon points="825,375 825,592 718,484" fill="var(--shape-grey)"/>
      <polygon points="128,0 698,0 825,365 538,647 10,120" fill="url(#officeScene)" stroke="var(--white)" stroke-width="12" role="img" aria-label="Financial advisor meeting with a client at a desk in a bright office"/>
    </svg>
    <h2 class="section-title specialist-title">Partner with a<br><span class="accent">Specialist</span></h2>
    <svg class="swoosh specialist-swoosh" viewBox="0 0 128 26"><path d="M2 14 C30 -2 70 2 90 14 C105 22 118 22 126 18 C110 26 92 24 80 18 C60 8 30 6 2 14Z" fill="var(--brand-grey)"/></svg>
    <p class="body-copy specialist-intro">Understanding your unique needs and vision for the future is<br>the starting point for our relationship. Together, we’ll assess<br>where you are financially and where you want to be. Next, we’ll create<br>a comprehensive wealth management plan that addresses your<br>immediate and long-term goals. What about the unpredictable? We’ll plan for<br>the changes that may be ahead, too.</p>
    <p class="body-copy specialist-outro">Exploring the topics of interest presented in this brochure will give you an idea of the depth and breadth of our services. Rest assured that we’ll partner with you throughout the planning process, always circling back to this fundamental question: what’s right for you and your loved ones?</p>
    <footer class="page-footer">www.themoskahouse.com</footer>
  </section>

  <!-- Our Firm -->
  <section class="page page--firm">
    <svg class="page-art" viewBox="0 0 825 1067">
      <defs>
        <linearGradient id="meetingScene" x1="0" y1="0" x2="1" y2="1">
          <stop offset="0" stop-color="#3b3f45"/>
          <stop offset="0.5" stop-color="#9aa3a8"/>
          <stop offset="1" stop-color="#5d6268"/>
        </linearGradient>
      </defs>
      <polygon points="362,0 825,0 825,165 607,235" fill="url(#meetingScene)" stroke="var(--white)" stroke-width="10" role="img" aria-label="Advisors in conversation around a meeting table"/>
      <polygon points="732,95 800,165 732,235 664,165" fill="var(--shape-grey)" stroke="var(--white)" stroke-width="8"/>
    </svg>
    <h2 class="section-title firm-title">Our <span class="accent">Firm</span></h2>
    <svg class="swoosh firm-swoosh" viewBox="0 0 128 26"><path d="M2 14 C30 -2 70 2 90 14 C105 22 118 22 126 18 C110 26 92 24 80 18 C60 8 30 6 2 14Z" fill="var(--brand-grey)"/></svg>
    <div class="body-copy firm-intro">
      <p>The Moska House LLC, established in 1987, is an independent,<br>full-service, financial consulting firm.</p>
      <p>As we search the marketplace for innovative, strategic solutions,<br>The Moska House is guided by the following principles:</p>
    </div>

    <div class="principles">
      <article class="principle">
        <svg class="principle-icon" viewBox="0 0 42 34" aria-hidden="true">
          <circle cx="14" cy="20" r="9" fill="none" stroke="var(--brand-grey)" stroke-width="6" stroke-dasharray="4 3"/>
          <circle cx="14" cy="20" r="3" fill="var(--brand-grey)"/>
          <circle cx="32" cy="9" r="5" fill="none" stroke="var(--brand-grey)" stroke-width="4"/>
          <circle cx="32" cy="27" r="4" fill="none" stroke="var(--brand-grey)" stroke-width="3"/>
        </svg>
        <h3 class="principle-name">Service</h3>
        <p class="principle-text">We seek to anticipate your needs and exceed your expectations in every aspect of our partnership.</p>
      </article>
      <article class="principle">
        <svg class="principle-icon" viewBox="0 0 42 34" aria-hidden="true">
          <rect x="14" y="2" width="20" height="28" fill="none" stroke="var(--brand-grey)" stroke-width="2.5"/>
          <line x1="18" y1="10" x2="30" y2="10" stroke="var(--brand-grey)" stroke-width="2"/>
          <line x1="18" y1="16" x2="30" y2="16" stroke="var(--brand-grey)" stroke-width="2"/>
          <line x1="18" y1="22" x2="26" y2="22" stroke="var(--brand-grey)" stroke-width="2"/>
        </svg>
        <h3 class="principle-name">Planning</h3>
        <p class="principle-text">We collaborate with you by listening, asking questions, educating and helping you make informed decisions to skillfully implement appropriate, effective financial strategies.</p>
      </article>
      <article class="principle">
        <svg class="principle-icon" viewBox="0 0 42 34" aria-hidden="true">
          <rect x="3" y="9" width="32" height="23" rx="3" fill="var(--brand-grey)"/>
          <rect x="12" y="3" width="14" height="8" rx="2" fill="none" stroke="var(--brand-grey)" stroke-width="3"/>
          <line x1="10" y1="11" x2="10" y2="32" stroke="var(--panel)" stroke-width="2"/>
          <line x1="28" y1="11" x2="28" y2="32" stroke="var(--panel)" stroke-width="2"/>
        </svg>
        <h3 class="principle-name">Integrity</h3>
        <p class="principle-text">We build long-term client relationships and are proud of the integrity and sensitivity we exhibit when working with all our clients.</p>
      </article>
    </div>

    <div class="firm-copy">
      <p class="firm-body">The Moska House has created an environment of objectivity and independence in which to provide independent guidance and access to the widest variety of fiscal tools to support your financial goals. Our work complements the services of your existing advisors, including CPAs and attorneys.* The degree and sophistication of the plan varies according to your circumstances.</p>
      <p class="firm-note">The Moska House LLC does not provide specific tax or legal advice. Please consult your accountant and/or attorney regarding your specific situation.</p>
    </div>

    <div class="firm-photo firm-photo--glass" role="img" aria-label="Modern glass office tower under a blue sky"></div>
    <div class="firm-photo firm-photo--modern" role="img" aria-label="Contemporary office building entrance at dusk"></div>

    <footer class="page-footer">www.themoskahouse.com</footer>
  </section>

</div>
</body>
</html>
```